Flyer-Design für Schädlingsbekämpfung
Sehr gute Kommunikation! Produkt sehr gut!! Gerne wieder
Zielgruppe
Schädlingsbekämpfung- und Prophylaxe, Service Monitoring, Gastronomie und Industrie, alle Lebendsmittel verarbeitenden Betriebe
Aufgabenstellung
Schwerpunkt soll das HACCP Konzept sein, welches bei allen Lebensmittelverarbeiteten Betrieben gesetzlich vorgeschrieben ist,

```html
<!DOCTYPE html>
<html lang="de">
<head>
<meta charset="utf-8">
<title>Schädlingsfrei Flyer</title>
<link href="https://fonts.googleapis.com/css2?family=Roboto:wght@400;500;700&display=swap" rel="stylesheet">
<style>
:root{
  --green:#0f8a3c;
  --green-dark:#0b7a33;
  --mint:#e4f1e9;
  --ink:#111111;
  --text:#1c1c1c;
  --white:#ffffff;
  --bg:#ffffff;
}
*{box-sizing:border-box;margin:0;padding:0}
html,body{width:1200px;height:1083px;overflow:hidden;background:var(--bg)}
body{font-family:"Roboto",Arial,sans-serif;color:var(--text);position:relative}
.flyer{position:absolute;top:54px;width:489px;height:977px;background:var(--white);
  box-shadow:0 6px 28px rgba(0,0,0,.18);overflow:hidden}
.flyer--front{left:69px}
.flyer--back{left:647px}
.photo{position:absolute;left:0;top:0;width:100%}
.flyer--front .photo{height:496px;background:linear-gradient(160deg,#e9ecee 0%,#cfd4d8 45%,#8b95a3 75%,#c7ccd1 100%)}
.flyer--back .photo{height:300px;background:linear-gradient(160deg,#d9dcdf 0%,#f3f3f2 40%,#b8bdc2 75%,#e6e7e8 100%)}
.photo-curve{position:absolute;left:0;width:100%}
.call-box{position:absolute;left:0;top:86px;width:226px;height:73px;background:var(--green);
  border-radius:0 6px 6px 0;color:var(--white);font-weight:700;font-size:20px;line-height:27px;padding:9px 0 0 26px}
.headline{position:absolute;left:0;width:100%;text-align:center;color:var(--ink);font-weight:700}
.flyer--front .headline{top:528px;font-size:31px;line-height:40px}
.services{position:absolute;left:42px;top:678px;list-style:none;font-size:21px;line-height:30px;color:var(--ink)}
.services li{display:flex;align-items:center;gap:7px}
.services svg{width:19px;height:19px;flex:none}
.brand{position:absolute;display:flex;align-items:center;gap:12px}
.brand-name{color:var(--green);font-weight:500;line-height:1.15;text-align:right}
.brand-mark{border-radius:50%;background:var(--green);flex:none}
.flyer--front .brand{left:75px;top:813px}
.flyer--front .brand-name{font-size:19px}
.flyer--front .brand-mark{width:100px;height:100px}
.footer-bar{position:absolute;left:0;bottom:0;width:100%;height:37px;background:var(--green);
  color:var(--white);font-weight:700;font-size:15px;text-align:center;line-height:37px}
.flyer--back .headline{top:320px;font-size:25px;line-height:36px}
.principles{position:absolute;left:40px;top:402px;width:420px;list-style:none;font-size:16px;line-height:20px;color:var(--text)}
.principles li{display:flex;gap:13px;margin-bottom:7px}
.principles .num{width:24px;height:24px;border-radius:50%;background:var(--green);color:var(--white);
  font-weight:700;font-size:17px;line-height:24px;text-align:center;flex:none;margin-top:-2px}
.contact-panel{position:absolute;left:0;top:724px;width:100%;height:216px;background:var(--mint)}
.flyer--back .brand{left:78px;top:16px}
.flyer--back .brand-name{font-size:19px}
.flyer--back .brand-mark{width:100px;height:100px}
.address{position:absolute;left:0;top:131px;width:100%;text-align:center;font-size:15.5px;line-height:22px;color:var(--ink)}
.address strong{font-weight:700}
</style>
</head>
<body>

<section class="flyer flyer--front">
  <div class="photo" role="img" aria-label="Foto: lächelnder Schädlingsbekämpfer in Latzhose mit Sprühgerät, Daumen hoch, in einer Großküche"></div>
  <svg class="photo-curve" style="top:440px" width="489" height="70" viewBox="0 0 489 70" preserveAspectRatio="none">
    <path d="M0 22 Q244 70 489 0 L489 70 L0 70 Z" fill="var(--mint)"/>
    <path d="M0 30 Q244 80 489 12 L489 70 L0 70 Z" fill="var(--white)"/>
  </svg>
  <div class="call-box">Rufen Sie uns an:<br>0612 / 480 31 772</div>
  <h1 class="headline">Ihr Partner bei der<br>professionellen<br>Schädlingsbekämpfung!</h1>
  <ul class="services">
    <li><svg viewBox="0 0 20 20"><circle cx="10" cy="10" r="8.5" fill="none" stroke="var(--green)" stroke-width="1.8"/><path d="M5.5 10.5l3 3 6.5-7" fill="none" stroke="var(--green)" stroke-width="2"/></svg>HACCP-Service</li>
    <li><svg viewBox="0 0 20 20"><circle cx="10" cy="10" r="8.5" fill="none" stroke="var(--green)" stroke-width="1.8"/><path d="M5.5 10.5l3 3 6.5-7" fill="none" stroke="var(--green)" stroke-width="2"/></svg>Schädlingsbekämpfung &amp; -prophylaxe</li>
    <li><svg viewBox="0 0 20 20"><circle cx="10" cy="10" r="8.5" fill="none" stroke="var(--green)" stroke-width="1.8"/><path d="M5.5 10.5l3 3 6.5-7" fill="none" stroke="var(--green)" stroke-width="2"/></svg>Service Monitoring &amp; Dokumentation</li>
    <li><svg viewBox="0 0 20 20"><circle cx="10" cy="10" r="8.5" fill="none" stroke="var(--green)" stroke-width="1.8"/><path d="M5.5 10.5l3 3 6.5-7" fill="none" stroke="var(--green)" stroke-width="2"/></svg>Gastronomie &amp; Industrie</li>
  </ul>
  <div class="brand">
    <div class="brand-name">Schädlingsfrei<br>Christian Walberg<br>Bad Auenstein</div>
    <div class="brand-mark"></div>
  </div>
  <div class="footer-bar">www.scw-ba.de</div>
</section>

<section class="flyer flyer--back">
  <div class="photo" role="img" aria-label="Foto: Koch mit Kochmütze und weißer Jacke, Arme verschränkt, in einer Profiküche"></div>
  <svg class="photo-curve" style="top:258px" width="489" height="60" viewBox="0 0 489 60" preserveAspectRatio="none">
    <path d="M0 10 Q244 60 489 14 L489 60 L0 60 Z" fill="var(--mint)"/>
    <path d="M0 18 Q244 68 489 24 L489 60 L0 60 Z" fill="var(--white)"/>
  </svg>
  <h2 class="headline">Die 7 Prinzipien des<br>HACCP-Konzepts:</h2>
  <ol class="principles">
    <li><span class="num">1</span><span>Durchführen einer Gefahrenanalyse</span></li>
    <li><span class="num">2</span><span>Identifikation der für die Sicherheit der Lebensmittel kritischen Kontrollpunkte</span></li>
    <li><span class="num">3</span><span>Festlegung von Eingreif- grenzen an den jeweiligen kritischen Kontrollpunkten</span></li>
    <li><span class="num">4</span><span>Einrichten von entsprechenden Überwachungs-verfahren an den kritischen Kontrollpunkten</span></li>
    <li><span class="num">5</span><span>Einrichten von Korrektur- maßnahmen für den Fall von Abweichungen</span></li>
    <li><span class="num">6</span><span>Einrichten von Evaluierungs- maßnahmen zur Überprüfung der Effizienz des festgelegten HACCP-Systems</span></li>
    <li><span class="num">7</span><span>Einrichten einer Dokumentation der Maßnahmen</span></li>
  </ol>
  <div class="contact-panel">
    <div class="brand">
      <div class="brand-name">Schädlingsfrei<br>Christian Walberg<br>Bad Auenstein</div>
      <div class="brand-mark"></div>
    </div>
    <p class="address"><strong>Schädlingsfrei Christian Walberg – Bad Auenstein</strong><br>Lindenallee 14-16 • 55321 Bad Auenstein<br>Tel.: 0612 / 480 31 772 • E-Mail: walberg(at)scw-ba.de</p>
  </div>
  <div class="footer-bar">www.scw-ba.de</div>
</section>

</body>
</html>
```